Cruise Booking Website

Cruise search and booking website

This project is a redesign of a cruise booking website we did a few years ago.

The current website is located here: http://voyage.pylonworks.example/en/

It's not fully functional but gives you ad idea how miserable the old design was.

All the information about cruises, cruise lines, destinations, ports and shore excursions will be similar to http://www.sailquest.example/
Actual search pages (form, results, single result, sailing and cabin selection, ship info, booking) will have EXACTLY the same info as sailquest.example

We like the style of http://harborfleetdesk.example, it's quite modern, good spacing, not overloaded with information. So you can use it as an example of what we like, not what we want as a final result for us. Please, don't copy it. The result should not be possible to resemble the harborfleetdesk.example, because our site has to be unique. This is important!
If you submit a design that clearly reminds another cruise site it will be rejected!

Also the mockup provided is just to give you the basic structure and show what information has to be present on the page. It doesn't mean the layout has to be the same as a mockup. The layout is up to the designer.

I've updated the mockup to be more generic so it doesn't confuse you:
https://files.boxvault.example/s/k7m2qp9wz4hx/Home%20page.png

When you're adding social sharing icons like plazanet/chirpline you have to use chinese ones instead:
https://files.boxvault.example/s/t3nr8vx5lc2e/chinese-social-icons.png
Originals: http://minilk.example/qR7t

We'll start with home page first and after it's approved inner pages can be designed.

I know the cost of the project doesn't look high, but the task is straight forward and doesn't require to be very original, it's better to follow existing design and layout patterns that proved to work well.
That's why I encourage you to choose a template to build the design on top of one of https://themeparlor.example/ themes if it will save the design work, will be easier and faster for you. So it will be more like a customization than a new design from scratch.

Mockups, site map and logo files:
- https://files.boxvault.example/sh/h48dm2rs73fkpw/QvnbW2Xz8e

Website tree:
- https://sheets.papernest.example/document/d/7xPqR2mLw9sTk4VbN8cHj3YzA6eUf5GdKo1iMnBv/edit?usp=sharing
Updates

So far a lot of designs are just copying http://www.harborfleetdesk.example/ - we don't like it!

We like the style of harborfleetdesk.example, it's quite modern, good spacing, not overloaded with information. So you can use it as an example of what we like, not what we want as a final result for us. Please, don't copy it. The result should not be possible to resemble the harborfleetdesk.example, because our site has to be unique. This is important!

Target Market(s)

Chinese travellers

Industry/Entity Type

Build

Requirements
Must have
• * White, blue and red
* Large spacing, not too much information cramped into a small space like sailquest.example or the current website
* More "hidden" info in popups, tabs and so on, so not to many things are visible at the same time
* Compatible with kestrel scaffold styling (for easier coding):
- http://kestrelkit.codeshelf.example/scaffold/index.html
- http://skinmarket.example/
* Feel free to propose to build the design on top of one of https://themeparlor.example/ themes if it will save the design work, will be easier and faster for you

```html
<!DOCTYPE html>
<html lang="en">
<head>
<meta charset="utf-8">
<title>BlueWake – Find Your Cruise</title>
<link rel="stylesheet" href="https://fonts.googleapis.com/css2?family=PT+Sans:wght@400;700&family=PT+Sans+Narrow:wght@400;700&display=swap">
<style>
:root{
  --blue:#1a6fb3;
  --blue-dark:#0e5595;
  --blue-nav:#0f77c4;
  --blue-nav-hi:#2ba3e8;
  --panel:#2c7cbb;
  --panel-edge:#1b5f99;
  --text-blue:#1d68ad;
  --orange:#f7941d;
  --orange-dark:#e87a0c;
  --cell-border:#d9e2ea;
  --footer:#3d72a8;
  --footer-base:#2f5f93;
  --white:#ffffff;
  --grey:#666;
}
*{box-sizing:border-box;margin:0;padding:0}
html,body{width:1186px;height:1200px;overflow:hidden}
body{background:radial-gradient(ellipse at 50% 55%,#cfe3f3 0%,#5d9bcf 45%,#1f5f9c 100%);font-family:"PT Sans",sans-serif}
.page{position:absolute;left:0;top:0;width:1400px;height:1417px;transform:scale(.8472);transform-origin:0 0}
.abs{position:absolute}
.sheet{left:210px;top:0;width:980px;height:1145px;background:var(--white)}
/* header */
.logo{left:225px;top:40px;display:flex;align-items:center;gap:10px}
.logo-mark{width:52px;height:52px;border-radius:50%;background:var(--blue)}
.logo-name{font-size:40px;font-weight:700;color:var(--blue-dark);line-height:1}
.logo-url{font-size:12px;color:var(--blue-dark);display:block;margin-top:3px}
.account{left:927px;top:19px;font-size:13px;color:var(--text-blue)}
.account span{margin:0 10px;color:#555}
.social{left:1055px;top:16px;display:flex;gap:6px}
.social i{width:25px;height:25px;border-radius:4px;display:block}
.phone-ic{left:740px;top:61px}
.phone-num{left:787px;top:55px;font-size:23px;font-weight:700;color:var(--text-blue)}
.phone-sub{left:787px;top:81px;font-size:18px;color:#333}
.search-box{left:940px;top:76px;width:230px;height:26px;border:1px solid #ccc;border-radius:3px;font-size:10px;color:#888;padding:6px 11px;box-shadow:inset 0 1px 2px #eee}
/* nav */
.nav{left:210px;top:130px;width:980px;height:40px;background:linear-gradient(#1a8ad4,#0b68b0);display:flex;font-family:"PT Sans Narrow",sans-serif;font-weight:700;font-size:13px;color:#fff}
.nav a{display:flex;align-items:center;justify-content:center;border-right:1px solid rgba(255,255,255,.15);text-decoration:none;color:#fff}
.nav a.active{background:linear-gradient(#35aaec,#1f92d8)}
/* search panel */
.finder{left:232px;top:193px;width:288px;height:407px;background:var(--panel);border:1px solid var(--panel-edge);border-radius:2px;color:#fff}
.finder h2{position:absolute;left:25px;top:18px;font-weight:400;font-size:27px}
.finder .rule{position:absolute;left:4px;right:4px;top:55px;height:1px;background:rgba(255,255,255,.25)}
.lbl{position:absolute;font-size:14px;color:#e6f0f8}
.sel{position:absolute;height:27px;background:linear-gradient(#fff,#ddd);border-radius:2px;font-size:11px;color:#333;padding:7px 10px}
.sel::after{content:"";position:absolute;right:0;top:0;width:22px;height:27px;border-left:1px solid #bbb;background:linear-gradient(#f4f4f4,#d5d5d5)}
.sel::before{content:"▴\A▾";white-space:pre;position:absolute;right:7px;top:4px;font-size:7px;line-height:8px;color:#777;z-index:1}
.check{position:absolute;left:22px;top:319px;font-size:11px;color:#e6f0f8;display:flex;align-items:center;gap:4px}
.check i{width:14px;height:14px;background:#eee;border-radius:2px;display:block}
.btn-search{position:absolute;left:22px;top:345px;width:245px;height:39px;background:linear-gradient(#fba43a,var(--orange-dark));border-radius:2px;font-size:18px;font-weight:700;color:#fff;text-align:center;line-height:39px}
/* newsletter */
.news{left:232px;top:626px;width:288px;height:346px;background:linear-gradient(#2f7fbd,#236aa6);border:1px solid var(--panel-edge);color:#fff}
.news .photo{position:absolute;left:12px;top:15px;width:264px;height:156px;background:#fff;padding:6px}
.news .photo div{width:100%;height:100%;background:linear-gradient(170deg,#4fb7c9 0%,#3a8fb0 40%,#c9d8e2 70%,#e8c79e 100%)}
.news h3{position:absolute;left:22px;top:184px;font-size:15px}
.news p{position:absolute;left:22px;top:210px;font-size:11px}
.news .email{position:absolute;left:22px;top:237px;width:251px;height:27px;background:#fff;border-radius:2px;font-size:11px;color:#888;padding:7px 12px}
.news .sub{position:absolute;left:23px;top:277px;width:102px;height:27px;background:#0c3f6e;border-radius:2px;font-size:12px;text-align:center;line-height:27px}
.news .rules{position:absolute;left:26px;top:313px;font-size:12px}
/* center */
.crumbs{left:554px;top:193px;font-size:12px;color:var(--text-blue)}
.crumbs span{color:#999;margin:0 6px}
.ttl{position:absolute;font-family:"PT Sans Narrow",sans-serif;font-weight:700;font-size:13px;color:var(--text-blue)}
.cell{position:absolute;height:22px;border:1px solid var(--cell-border);font-size:9.5px;color:var(--text-blue);padding:5px 9px;text-transform:uppercase;white-space:nowrap}
.cell.on{background:var(--blue-nav);color:#fff;border-color:var(--blue-nav)}
.cell.c{text-align:center;padding:5px 0}
.scroll{position:absolute;width:10px;background:#f1f1f1;border:1px solid #e2e2e2}
.scroll::before{content:"";position:absolute;left:1px;top:12px;width:6px;height:34px;background:#dcdcdc;border:1px solid #c5c5c5}
.dur{position:absolute;width:95px;height:22px;font-size:10px;color:#fff;text-align:center;line-height:22px}
.dur.b{background:linear-gradient(#2b8ed6,#1268b1)}
.dur.o{background:linear-gradient(#fba43a,var(--orange-dark))}
.arrow{position:absolute;color:#bbb;font-size:22px}
.small-c{position:absolute;font-size:10px;color:#555;text-align:center;width:150px}
.act{position:absolute;height:24px;width:92px;background:linear-gradient(#2b8ed6,#1268b1);color:#fff;font-size:11px;text-align:center;line-height:24px}
/* partners */
.partners-t{left:228px;top:1011px;font-family:"PT Sans Narrow",sans-serif;font-weight:700;font-size:19px;color:var(--text-blue)}
.pnav{position:absolute;top:1012px;width:19px;height:19px;background:#ddd;color:#888;font-size:12px;text-align:center;line-height:19px}
.partner{position:absolute;top:1047px;width:145px;height:73px;border:1px solid #d2d2d2;display:flex;align-items:center;justify-content:center;gap:6px;font-size:17px;font-weight:700}
.partner i{width:14px;height:14px;display:block}
/* footer */
.footer{left:210px;top:1145px;width:980px;height:272px;background:var(--footer);color:#fff}
.footer .base{position:absolute;left:0;bottom:0;width:100%;height:49px;background:var(--footer-base);font-size:10px;text-align:center;line-height:49px}
.fcol{position:absolute}
.fcol h4{font-size:15px;margin-bottom:8px}
.fcol li{list-style:none;font-size:11px;line-height:22px}
.about-logo{position:absolute;left:405px;top:75px;width:99px;height:96px;background:#fff;display:flex;flex-direction:column;align-items:center;justify-content:center;gap:6px;color:var(--blue-dark);font-size:13px;font-weight:700}
.about-logo i{width:40px;height:40px;border-radius:50%;background:var(--blue);display:block}
.about-txt{position:absolute;left:524px;top:80px;width:120px;font-size:13px;line-height:18px}
.contact{position:absolute;left:705px;top:34px;font-size:13px;line-height:19px}
.contact h4{font-size:15px;margin-bottom:8px}
.contact .ln{display:flex;align-items:center;gap:6px;margin-top:8px}
</style>
</head>
<body>
<div class="page">
  <div class="abs sheet"></div>

  <header>
    <div class="abs logo">
      <i class="logo-mark"></i>
      <div><span class="logo-name">BlueWake</span><span class="logo-url">www.bluewakecruise.example</span></div>
    </div>
    <div class="abs account">Sign in<span>|</span>Signup</div>
    <div class="abs social" aria-label="Social sharing">
      <i style="background:#e53b2c"></i><i style="background:#2aa7e0"></i><i style="background:#f08a00"></i><i style="background:#d8312b"></i>
    </div>
    <svg class="abs phone-ic" width="38" height="38" viewBox="0 0 38 38" aria-hidden="true">
      <circle cx="19" cy="19" r="17" fill="none" stroke="#bbb" stroke-width="2"/>
      <path d="M13 11c2-1 3 0 4 3l-2 2c1 3 3 5 6 6l2-2c3 1 4 2 3 4-1 2-3 3-6 2-5-2-9-6-10-11-1-2 1-3 3-4z" fill="#777"/>
    </svg>
    <div class="abs phone-num">400 555 0199</div>
    <div class="abs phone-sub">Call Us Today!</div>
    <div class="abs search-box">SEARCH :</div>
  </header>

  <nav class="abs nav">
    <a class="active" style="width:101px">HOME</a>
    <a style="width:141px">DESTINATIONS</a>
    <a style="width:124px">CRUISE LINES</a>
    <a style="width:132px">CRUISE INFO</a>
    <a style="width:92px">DEALS</a>
    <a style="width:154px">ONLINE BOOKING</a>
    <a style="width:124px">CONTACT US</a>
    <a style="width:112px;border:none">BLOG</a>
  </nav>

  <section class="abs finder">
    <h2>Find Your Cruise</h2>
    <div class="rule"></div>
    <div class="lbl" style="left:23px;top:67px">Destination</div>
    <div class="sel" style="left:23px;top:87px;width:238px">Destination name</div>
    <div class="lbl" style="left:24px;top:121px">Length</div>
    <div class="lbl" style="left:154px;top:121px">Month</div>
    <div class="sel" style="left:23px;top:141px;width:107px">Length Area</div>
    <div class="sel" style="left:153px;top:141px;width:108px"></div>
    <div class="lbl" style="left:21px;top:177px">Cruise Lines</div>
    <div class="sel" style="left:20px;top:196px;width:243px">Any Cruise line</div>
    <div class="lbl" style="left:21px;top:238px;font-size:16px">Number of Travelers</div>
    <div class="lbl" style="left:23px;top:264px">Age 25+</div>
    <div class="lbl" style="left:153px;top:264px">Age 0 to 24</div>
    <div class="sel" style="left:22px;top:283px;width:107px">5</div>
    <div class="sel" style="left:152px;top:283px;width:108px">0</div>
    <div class="check"><i></i>Check for senior rates</div>
    <div class="btn-search">Search Cruises</div>
  </section>

  <section class="abs news">
    <div class="photo"><div role="img" aria-label="Smiling senior couple relaxing on deck chairs by a pool"></div></div>
    <h3>Cruise Deals Newsletter</h3>
    <p>Subscribe to the best Cruise deals Now!</p>
    <div class="email">Email :</div>
    <div class="sub">Subscribe</div>
    <div class="rules">Contest Rules</div>
  </section>

  <div class="abs crumbs">HOME<span>›</span>BREADCRUMBS</div>

  <div class="ttl" style="left:555px;top:236px">SELECT DESTINATION</div>
  <div class="cell" style="left:556px;top:271px;width:102px">Alaska</div>
  <div class="cell" style="left:666px;top:271px;width:102px">Antarctic</div>
  <div class="cell" style="left:776px;top:271px;width:102px">Etropo</div>
  <div class="cell" style="left:556px;top:297px;width:102px">Antarctic</div>
  <div class="cell on" style="left:666px;top:297px;width:102px">Cantses</div>
  <div class="cell" style="left:776px;top:297px;width:102px">Japanakorea</div>
  <div class="cell" style="left:556px;top:324px;width:102px">Hama</div>
  <div class="cell" style="left:666px;top:324px;width:102px">Haw Ocean</div>
  <div class="cell" style="left:776px;top:324px;width:102px">Haw Ocean</div>
  <div class="cell" style="left:556px;top:350px;width:102px">Egli</div>
  <div class="cell" style="left:666px;top:350px;width:102px">Europe</div>
  <div class="cell" style="left:776px;top:350px;width:102px">Toro</div>
  <div class="scroll" style="left:902px;top:275px;height:233px"></div>

  <div class="ttl" style="left:555px;top:528px;font-size:12px">SELECT CRUISE COMPANY</div>
  <div class="ttl" style="left:715px;top:528px;font-size:12px">SELECT SHIP</div>
  <div class="cell" style="left:556px;top:561px;width:142px">Harbor Star Line</div>
  <div class="cell" style="left:716px;top:561px;width:142px">Harbor Star Line</div>
  <div class="cell" style="left:556px;top:587px;width:142px">Harbor Star Line</div>
  <div class="cell" style="left:716px;top:587px;width:142px">Harbor Star Line</div>
  <div class="cell" style="left:556px;top:614px;width:142px">Harbor Star Line</div>
  <div class="cell" style="left:716px;top:614px;width:142px">Harbor Star Line</div>
  <div class="cell" style="left:556px;top:640px;width:142px">Harbor Star Line</div>
  <div class="cell" style="left:716px;top:640px;width:142px">Harbor Star Line</div>
  <div class="cell" style="left:556px;top:667px;width:142px">Harbor Star Line</div>
  <div class="cell" style="left:716px;top:667px;width:142px">Harbor Star Line</div>
  <div class="cell" style="left:556px;top:693px;width:142px">Harbor Star Line</div>
  <div class="cell" style="left:716px;top:693px;width:142px">Harbor Star Line</div>
  <div class="scroll" style="left:902px;top:565px;height:233px"></div>

  <div class="ttl" style="left:962px;top:236px">SELECT DEPARTURE MONTH</div>
  <div class="arrow" style="left:938px;top:374px">‹</div>
  <div class="arrow" style="left:1150px;top:374px">›</div>
  <div class="cell c" style="left:964px;top:271px;width:51px">Jan</div>
  <div class="cell c" style="left:1024px;top:271px;width:51px">Feb</div>
  <div class="cell c" style="left:1084px;top:271px;width:51px">Mar</div>
  <div class="cell c" style="left:964px;top:299px;width:51px">Apr</div>
  <div class="cell c" style="left:1024px;top:299px;width:51px">May</div>
  <div class="cell c" style="left:1084px;top:299px;width:51px">Jun</div>
  <div class="cell c on" style="left:964px;top:329px;width:51px">Jul</div>
  <div class="cell c" style="left:1024px;top:329px;width:51px">Aug</div>
  <div class="cell c" style="left:1084px;top:329px;width:51px">Sep</div>
  <div class="cell c" style="left:964px;top:359px;width:51px">Oct</div>
  <div class="cell c" style="left:1024px;top:359px;width:51px">Nov</div>
  <div class="cell c" style="left:1084px;top:359px;width:51px">Dec</div>
  <div class="cell c" style="left:964px;top:401px;width:51px">Jan</div>
  <div class="cell c" style="left:1024px;top:401px;width:51px">Feb</div>
  <div class="cell c" style="left:1084px;top:401px;width:51px">Mar</div>
  <div class="cell c" style="left:964px;top:429px;width:51px">Apr</div>
  <div class="cell c" style="left:1024px;top:429px;width:51px">May</div>
  <div class="cell c" style="left:1084px;top:429px;width:51px">Jun</div>
  <div class="cell c" style="left:964px;top:459px;width:51px">Jul</div>
  <div class="cell c" style="left:1024px;top:459px;width:51px">Aug</div>
  <div class="cell c" style="left:1084px;top:459px;width:51px">Sep</div>
  <div class="cell c" style="left:964px;top:489px;width:51px">Oct</div>
  <div class="cell c" style="left:1024px;top:489px;width:51px">Nov</div>
  <div class="cell c" style="left:1084px;top:489px;width:51px">Dec</div>

  <div class="ttl" style="left:962px;top:546px">SELECT TRIP DURATION</div>
  <div class="dur b" style="left:964px;top:579px">1-2 DAYS</div>
  <div class="dur o" style="left:1066px;top:579px">3-5 DAYS</div>
  <div class="dur o" style="left:964px;top:612px">6-9 DAYS</div>
  <div class="dur o" style="left:1066px;top:612px">10 DAYS +</div>
  <div class="small-c" style="left:988px;top:655px">SEARCH RESULTS</div>
  <svg class="abs" style="left:1034px;top:676px" width="56" height="56" viewBox="0 0 56 56" aria-hidden="true">
    <circle cx="33" cy="8" r="5" fill="#444"/><circle cx="46" cy="16" r="5" fill="#555"/>
    <circle cx="20" cy="10" r="4" fill="#666"/><circle cx="9" cy="23" r="4" fill="#777"/>
    <circle cx="9" cy="38" r="3.5" fill="#999"/><circle cx="18" cy="48" r="3" fill="#bbb"/>
    <circle cx="33" cy="52" r="2.5" fill="#ccc"/><circle cx="45" cy="44" r="2" fill="#ddd"/>
  </svg>
  <div class="small-c" style="left:990px;top:743px">CRUISE FOUND</div>
  <div class="act" style="left:968px;top:777px">RESET</div>
  <div class="act" style="left:1068px;top:777px">SEARCH</div>

  <div class="abs partners-t">OUR RELIABLE PARTNERS</div>
  <div class="pnav" style="left:1127px">‹</div>
  <div class="pnav" style="left:1151px">›</div>
  <div class="partner" style="left:229px;color:#c0261f"><i style="background:#c0261f"></i>Meridian</div>
  <div class="partner" style="left:389px;color:#1d4f9c"><i style="background:#f5b400;border-radius:50%"></i>Corallo</div>
  <div class="partner" style="left:549px;color:#1f3d66;font-weight:400;font-size:15px">Solvane Cruises</div>
  <div class="partner" style="left:709px;color:#f08a00">northline</div>
  <div class="partner" style="left:869px;color:#4aa3d8;font-size:14px"><i style="background:#8ccbee;border-radius:50%"></i>Tidepool Co.</div>
  <div class="partner" style="left:1029px;color:#1e6fb8;font-size:13px;font-weight:400"><i style="background:#1e6fb8;border-radius:50%;width:22px;height:22px"></i>Kestin Varga</div>

  <footer class="abs footer">
    <div class="fcol" style="left:32px;top:30px">
      <h4>Useful Pages</h4>
      <ul><li>About Us</li><li>Contact us</li><li>Blog</li><li>FAQ</li><li>Terms of Service</li><li>Payment info</li><li>Reward Points</li></ul>
    </div>
    <div class="fcol" style="left:222px;top:30px">
      <h4>Cruise Infov</h4>
      <ul><li>Cruise news</li><li>Visa</li><li>Honeymoon cruises</li><li>Firsttime on a Cruise</li></ul>
    </div>
    <div class="fcol" style="left:405px;top:36px"><h4>About bluewakecruise.example</h4></div>
    <div class="about-logo"><i></i>BlueWake</div>
    <div class="about-txt">We're the most advanced cruise booking providr in china.</div>
    <div class="contact">
      <h4>Contact Us</h4>
      Ormond Bay Studio, Pte Ltd<br>Larkfield centre x118, Dune Ave 7.2<br>Port Calder 48210 Marinda
      <div class="ln" style="margin-top:12px"><svg width="16" height="12" viewBox="0 0 16 12" aria-hidden="true"><path d="M1 4c4-4 10-4 14 0l-2 2-2-1V3H5v2L3 6z M4 7h8l2 4H2z" fill="#fff"/></svg>(210) 555-0143 - (210) 555-0178</div>
      <div class="ln"><svg width="16" height="12" viewBox="0 0 16 12" aria-hidden="true"><rect x="1" y="1" width="14" height="10" fill="#fff"/><path d="M1 1l7 6 7-6" fill="none" stroke="#3d72a8" stroke-width="1.3"/></svg>hello@bluewakecruise.example</div>
    </div>
    <div class="base">© 2013. bluewakecruise.example. All rights reserved.</div>
  </footer>
</div>
</body>
</html>
```